Want to fly? Flight school needs a roll up

Hello designers

We are a small aviation club with around 100 members. We love flying and therefore offer free flight lessons for young people at our glider flight school.
The young people only have to pay a flat rate of €300 for the aircraft until their first solo flight.
To advertise the flight school we now need a roll up banner measuring 85cm x 200cm. You can find the data sheet for the banner in the appendix.
Content of the roll up banner:
Advertising for our flight school so that we can attract new members
The banner should be designed in our club colors blue/white
The banner is aimed at all people who want to get a glider license
A great offer for young people up to the age of 25 should be placed on the banner with a reference to the text “Offer only applies to people up to the age of 25. Included in the flat rate of €300 is training on the glider up to the first "solo flight"
The banner is intended to advertise training with a glider. Therefore the wish would be for a glider to be depicted

Here is a link to our current homepage

https://www.lgk-tarnholm.de/

https://www.vidoplex.example/watch?v=Qk7pL2xNz9c

Target Market(s)

Young people from 14 years to 30 years

Colors
0054AA
0677BA
7BADD7
CADEEF
E8F1F8

Requirements
Nice to have
• Glider / club logo
Should not have
• Too much text

```html
<!DOCTYPE html>
<html lang="en">
<head>
<meta charset="utf-8">
<title>Luftsportgruppe Tarnholm – Free Flight Lessons Roll-up</title>
<link href="https://fonts.googleapis.com/css2?family=Archivo+Black&family=Bebas+Neue&family=Poppins:wght@400;500;600;700&display=swap" rel="stylesheet">
<style>
  :root {
    --club-blue: #0a1ea8;
    --club-blue-deep: #0816a0;
    --ink: #2b2b33;
    --white: #ffffff;
    --offer-red: #e4101c;
    --page: #f7f9fb;
    --rule: #c9cdd6;
  }
  * { margin: 0; padding: 0; box-sizing: border-box; }
  html, body { width: 1200px; height: 3000px; overflow: hidden; background: var(--white); }
  .rollup {
    position: relative;
    width: 1200px;
    height: 3000px;
    overflow: hidden;
    font-family: "Poppins", sans-serif;
    background: linear-gradient(180deg, #ffffff 0%, #fafbfd 55%, #eef2f6 100%);
  }
  .hero { position: absolute; left: 0; top: 0; width: 1200px; height: 1250px; }

  .club-mark { position: absolute; left: 110px; top: 680px; width: 330px; text-align: center; }
  .club-mark__circle {
    width: 190px; height: 190px; margin: 0 auto 22px;
    border: 10px solid var(--club-blue); border-radius: 50%;
  }
  .club-mark__name { font-weight: 700; font-size: 30px; line-height: 1.2; color: var(--club-blue); }

  .headline { position: absolute; left: 113px; white-space: nowrap; }
  .headline--free {
    top: 1080px; font-family: "Archivo Black", sans-serif; font-size: 190px;
    line-height: 1; color: var(--ink); letter-spacing: -4px;
  }
  .headline--lessons {
    top: 1250px; font-family: "Bebas Neue", sans-serif; font-size: 212px;
    line-height: 1; color: var(--club-blue); letter-spacing: -2px;
  }
  .headline--audience {
    top: 1440px; font-weight: 600; font-size: 86px; line-height: 1; color: var(--ink); letter-spacing: -1px;
  }
  .headline--school {
    top: 1555px; font-weight: 600; font-size: 40px; line-height: 1; color: var(--club-blue); letter-spacing: 9px;
  }

  .offer-box {
    position: absolute; left: 113px; top: 1652px; width: 880px; height: 248px;
    background: var(--club-blue-deep); border-radius: 36px 0 0 36px;
    padding: 26px 0 0 44px; color: var(--white);
    font-size: 50px; line-height: 1.2; font-weight: 500;
  }
  .offer-box strong { font-weight: 700; font-size: 58px; }
  .price-badge {
    position: absolute; left: 800px; top: 1650px; width: 252px; height: 252px;
    border-radius: 50%; background: var(--white); border: 6px solid var(--club-blue-deep);
    display: flex; align-items: center; justify-content: center;
  }
  .price-badge__inner {
    width: 220px; height: 220px; border-radius: 50%; background: var(--offer-red);
    display: flex; align-items: center; justify-content: center;
    font-family: "Bebas Neue", sans-serif; font-size: 128px; color: var(--white); line-height: 1; padding-top: 10px;
  }
  .price-badge__inner sup { font-size: 56px; vertical-align: top; margin-top: -10px; margin-right: 2px; }

  .crew-photo {
    position: absolute; left: 700px; top: 1990px; width: 500px; height: 1010px;
    background:
      radial-gradient(ellipse 60% 18% at 52% 14%, rgba(214,170,140,0.55) 0%, rgba(214,170,140,0) 100%),
      radial-gradient(ellipse 45% 10% at 50% 80%, rgba(238,196,40,0.55) 0%, rgba(238,196,40,0) 100%),
      linear-gradient(180deg, rgba(247,249,251,0) 0%, #e3e9f0 8%, #d7e0ea 22%, #2f66b8 40%, #2558a8 70%, #1e4e98 88%, #cfd6de 100%);
  }

  .training-list { position: absolute; left: 120px; top: 1930px; width: 720px; list-style: none; }
  .training-list__item { position: relative; height: 240px; display: flex; align-items: center; }
  .training-list__item + .training-list__item::before {
    content: ""; position: absolute; left: 200px; right: 90px; top: 0; height: 2px; background: var(--rule);
  }
  .training-list__icon {
    width: 184px; height: 184px; flex: none; border-radius: 50%;
    border: 8px solid var(--club-blue-deep);
    box-shadow: inset 0 0 0 5px var(--white);
  }
  .icon--gliding { background: linear-gradient(160deg, #e6ecf0, #a9b6c0 55%, #6f7e88); }
  .icon--motor { background: linear-gradient(180deg, #8aa860 0%, #5f8e3c 55%, #b9c78c 100%); }
  .icon--powered { background: linear-gradient(180deg, #cfdbe7 0%, #a6bacd 55%, #3f6a3a 100%); }
  .training-list__label {
    margin-left: 30px; font-weight: 700; font-size: 56px; line-height: 1.02; color: var(--ink); white-space: nowrap;
  }

  .age-note { position: absolute; left: 113px; top: 2690px; font-size: 37px; line-height: 1.1; color: var(--ink); }
  .age-note strong { color: var(--club-blue); font-weight: 700; }

  .web-bar {
    position: absolute; left: 0; top: 2808px; width: 932px; height: 72px;
    background: var(--club-blue-deep); border-radius: 0 36px 36px 0;
    border: 3px solid var(--white); border-left: none;
    display: flex; align-items: center; padding-left: 113px;
    color: var(--white); font-weight: 700; font-size: 44px; letter-spacing: 6px;
  }
</style>
</head>
<body>
<main class="rollup">

  <svg class="hero" viewBox="0 0 1200 1250" xmlns="http://www.w3.org/2000/svg">
    <defs>
      <linearGradient id="skyFade" x1="0" y1="0" x2="0" y2="1">
        <stop offset="0" stop-color="#8fb0d0"/>
        <stop offset="0.35" stop-color="#cddcea"/>
        <stop offset="0.7" stop-color="#eef3f8"/>
        <stop offset="1" stop-color="#ffffff" stop-opacity="0"/>
      </linearGradient>
      <radialGradient id="cloudGlow" cx="0.5" cy="0.5" r="0.5">
        <stop offset="0" stop-color="#ffffff" stop-opacity="0.9"/>
        <stop offset="1" stop-color="#ffffff" stop-opacity="0"/>
      </radialGradient>
      <linearGradient id="landscape" x1="0" y1="0" x2="0" y2="1">
        <stop offset="0" stop-color="#8fb6bc"/>
        <stop offset="0.55" stop-color="#b9d0d1"/>
        <stop offset="0.72" stop-color="#50603a"/>
        <stop offset="0.85" stop-color="#7a7444"/>
        <stop offset="1" stop-color="#a08a54"/>
      </linearGradient>
    </defs>
    <g role="img" aria-label="Sky with clouds behind an aerobatic aircraft in flight">
      <rect x="0" y="0" width="1200" height="1250" fill="url(#skyFade)"/>
      <ellipse cx="280" cy="260" rx="360" ry="150" fill="url(#cloudGlow)"/>
      <ellipse cx="120" cy="560" rx="260" ry="110" fill="url(#cloudGlow)"/>
    </g>
    <path role="img" aria-label="Aircraft banking over a forest and meadow landscape"
          d="M770 0 L1200 0 L1200 1050 C1030 1105 800 1080 640 960 C500 850 440 700 470 600 Z"
          fill="url(#landscape)"/>
    <path d="M770 0 L465 600" stroke="#ffffff" stroke-width="10" fill="none"/>
    <path class="swoosh" d="M470 600 C430 760 520 930 700 1040 C860 1130 1040 1120 1200 1050 L1200 1160 C1040 1230 820 1220 650 1100 C470 970 400 780 470 600 Z"
          fill="var(--club-blue-deep)"/>
  </svg>

  <div class="club-mark">
    <div class="club-mark__circle"></div>
    <p class="club-mark__name">Luftsportgruppe Tarnholm e.V.</p>
  </div>

  <h1 class="headline headline--free">FREE</h1>
  <p class="headline headline--lessons">FLIGHT LESSONS</p>
  <p class="headline headline--audience">FOR YOUNG PEOPLE</p>
  <p class="headline headline--school">AT OUR GLIDER FLIGHT SCHOOL</p>

  <div class="offer-box">TRAINING ON THE<br>GLIDER UP TO THE FIRST<br><strong>"SOLO FLIGHT"</strong> IS</div>
  <div class="price-badge"><div class="price-badge__inner"><sup>€</sup>300</div></div>

  <div class="crew-photo" role="img" aria-label="Smiling pilot in a blue uniform with yellow gloves standing in front of an airliner"></div>

  <ul class="training-list">
    <li class="training-list__item">
      <div class="training-list__icon icon--gliding" role="img" aria-label="Glider cockpit"></div>
      <span class="training-list__label">GLIDING</span>
    </li>
    <li class="training-list__item">
      <div class="training-list__icon icon--motor" role="img" aria-label="Motor glider on a grass airfield"></div>
      <span class="training-list__label">MOTOR GLIDER</span>
    </li>
    <li class="training-list__item">
      <div class="training-list__icon icon--powered" role="img" aria-label="Light aircraft taking off"></div>
      <span class="training-list__label">POWERED<br>FLIGHT</span>
    </li>
  </ul>

  <p class="age-note">OFFER ONLY APPLIES TO<br>PEOPLE UP TO THE AGE OF <strong>25</strong></p>

  <div class="web-bar">www.lgk-tarnholm.de</div>

</main>
</body>
</html>
```